Dorwin's Coating & Renewal Letterhead Design We want to revamp out old traditional letterhead with the new logo designs that are attached. We are working on getting all our company items from vehicles, business, cards, t-shirts, letterhead to match. This should include company colors, fonts, and flow of items that we have attached below.

Industry/Entity Type

Construction Company

Font styles to use
Sans Serif
Other font styles liked:
• Bold with outline

Colors
ec1f27
ffffff

Requirements
Must have
• Company Name: Dorwin's Coating & Renewal
• Address: 4728 SW 81st Ter Halverd cove fl 39417
• Office Number: (555) 413-2986
• Email: Dorwinrenewal@mailbrook.example
• License Number: KRT8046392
Nice to have
• Company Colors: red, white, black, and grey

```html
<!DOCTYPE html>
<html lang="en">
<head>
<meta charset="utf-8">
<title>Dorwin's Coating &amp; Renewal Letterhead</title>
<link href="https://fonts.googleapis.com/css2?family=Montserrat:wght@400;600;700&display=swap" rel="stylesheet">
<style>
  :root {
    --brand-red: #ec1f27;
    --ink: #333333;
    --ink-dark: #2b2b2b;
    --swoosh-grey: #e6e6e6;
    --pattern-grey: #f1f1f1;
    --paper: #ffffff;
    --blush: #fbd9d0;
  }
  * { margin: 0; padding: 0; box-sizing: border-box; }
  html, body { width: 904px; height: 1200px; overflow: hidden; background: var(--paper); }
  body { font-family: "Montserrat", sans-serif; color: var(--ink); }
  .letterhead { position: relative; width: 904px; height: 1200px; overflow: hidden; background: var(--paper); }
  .decor { position: absolute; inset: 0; width: 904px; height: 1200px; }
  .pattern-area {
    position: absolute; left: 0; top: 720px; width: 904px; height: 400px;
    background: linear-gradient(170deg, rgba(241,241,241,0) 0%, var(--pattern-grey) 40%, rgba(241,241,241,0.4) 80%, rgba(255,255,255,0) 100%);
    clip-path: polygon(0 45%, 40% 30%, 75% 14%, 100% 0, 100% 62%, 60% 75%, 0 100%);
  }
  .brand-name {
    position: absolute; left: 64px; top: 58px; width: 300px;
    font-weight: 700; color: var(--brand-red); text-transform: uppercase;
    line-height: 1.1;
  }
  .brand-name .primary { display: block; font-size: 34px; letter-spacing: 1px; }
  .brand-name .secondary { display: block; font-size: 18px; letter-spacing: 2px; }
  .contact { position: absolute; right: 59px; top: 52px; text-align: right; font-weight: 600; font-size: 15px; color: var(--ink-dark); }
  .contact-line { display: flex; align-items: center; justify-content: flex-end; gap: 8px; height: 19.5px; }
  .contact-icon { width: 16px; height: 16px; flex: none; }
  .rule-top { position: absolute; left: 377px; right: 0; top: 136px; height: 2px; background: var(--brand-red); }
  .signoff { position: absolute; left: 64px; top: 238px; font-size: 13px; }
  .signer-name { position: absolute; left: 64px; top: 271px; font-size: 22px; font-weight: 700; color: var(--ink-dark); letter-spacing: 0.3px; }
  .signer-title { position: absolute; left: 64px; top: 300px; font-size: 15px; font-weight: 600; color: var(--ink-dark); }
  .body-copy { position: absolute; left: 64px; width: 790px; font-size: 13.4px; line-height: 28px; }
  .body-copy.p1 { top: 459px; }
  .body-copy.p2 { top: 654px; }
  .body-copy.p3 { top: 794px; }
  .rule-bottom { position: absolute; left: 0; right: 0; top: 1143px; height: 2px; background: var(--brand-red); }
  .footer { position: absolute; left: 64px; right: 59px; top: 1160px; display: flex; justify-content: space-between; font-weight: 700; font-size: 16.5px; }
  .footer .address { color: var(--ink-dark); }
  .footer .license { color: var(--brand-red); }
</style>
</head>
<body>
<div class="letterhead">
  <svg class="decor" viewBox="0 0 904 1200" aria-hidden="true">
    <path d="M0 270 C 300 250, 600 150, 750 0 L 820 0 C 660 160, 330 270, 0 282 Z" fill="var(--swoosh-grey)"/>
    <path d="M520 212 C 690 170, 840 100, 904 28 L 904 58 C 830 130, 690 185, 520 212 Z" fill="var(--swoosh-grey)"/>
    <path d="M240 1200 C 330 1150, 420 1110, 530 1085 C 430 1115, 330 1160, 280 1200 Z" fill="var(--blush)" opacity="0.8"/>
    <path d="M510 1200 C 640 1140, 780 1100, 904 1082 L 904 1090 C 790 1110, 660 1150, 560 1200 Z" fill="var(--blush)" opacity="0.8"/>
  </svg>
  <div class="pattern-area" role="img" aria-label="Faint grey halftone dot pattern band"></div>

  <div class="brand-name">
    <span class="primary">Dorwin's</span>
    <span class="secondary">Coating &amp; Renewal</span>
  </div>

  <div class="contact">
    <div class="contact-line">(555) 413-2986
      <svg class="contact-icon" viewBox="0 0 16 16"><circle cx="8" cy="8" r="7" fill="none" stroke="var(--brand-red)" stroke-width="1.2"/><path d="M5.4 4.6 L6.6 4.4 L7.3 6.2 L6.5 6.9 C6.9 7.9 7.8 8.8 8.9 9.3 L9.6 8.5 L11.4 9.2 L11.2 10.4 C8 10.6 5.2 7.8 5.4 4.6 Z" fill="var(--brand-red)"/></svg>
    </div>
    <div class="contact-line">Dorwinrenewal@mailbrook.example
      <svg class="contact-icon" viewBox="0 0 16 16"><circle cx="8" cy="8" r="7" fill="none" stroke="var(--brand-red)" stroke-width="1.2"/><rect x="4.5" y="5.5" width="7" height="5" fill="var(--brand-red)"/><path d="M4.5 5.5 L8 8.3 L11.5 5.5" fill="none" stroke="#fff" stroke-width="0.8"/></svg>
    </div>
    <div class="contact-line">www.dorwinrenewal.example
      <svg class="contact-icon" viewBox="0 0 16 16"><circle cx="8" cy="8" r="7" fill="none" stroke="var(--brand-red)" stroke-width="1.2"/><circle cx="8" cy="8" r="3.8" fill="none" stroke="var(--brand-red)" stroke-width="0.8"/><ellipse cx="8" cy="8" rx="1.6" ry="3.8" fill="none" stroke="var(--brand-red)" stroke-width="0.8"/><path d="M4.2 8 H11.8" stroke="var(--brand-red)" stroke-width="0.8"/></svg>
    </div>
  </div>
  <div class="rule-top"></div>

  <p class="signoff">Sincearly,</p>
  <p class="signer-name">LORNE DORWIN II</p>
  <p class="signer-title">Owner/Supervisor</p>

  <p class="body-copy p1">This is a sample letter that has been placed to demonstrate typing remat (Your Company).letterhead design. When positioned properly, it will serve to work in harmony with all other elements letterhead. This letterhead design is meant to project an image&nbsp; This letterhead design is meant project an image of professionalism reliability. By using simple aligen we have created a very spacious feeling. The simplicity suggest&nbsp; rengththe spaciousnes contributes haesthetics the layout. These basic qualities along with the (Your Company)</p>
  <p class="body-copy p2">look and helps reinforce the (Your Company) brand. letterhead design is meant to project an image design. When positioned properly, it will serve to work in harmony all the other elements letterhead. sionalism and reliability.</p>
  <p class="body-copy p3">This letterhead design is based on the (Form of your logo) form (Your Company) logo. Each stationery we have created a very spacious feeling. The simplicity suggests strength the spaciousnes contribute part of the (Form of your logo). This letterhead design is based on the (Form of your logo) form (Your Company) logo. Each stationery we have created a very spacious feeling. The simplicity suggests strength the spaciousnes contribute part of the (Form of your logo).</p>

  <div class="rule-bottom"></div>
  <div class="footer">
    <span class="address">4728 SW 81st Ter . Halverd Cove, Florida 39417</span>
    <span class="license">KRT8046392</span>
  </div>
</div>
</body>
</html>
```